KTR Design Business Card

I need to develop a business card for my real estate design and investment company. Something clean, classic and professional with a modern vibe.

Industry/Entity Type

Real Estate

Font styles to use
Serif
Sans Serif

```html
<!DOCTYPE html>
<html lang="en">
<head>
<meta charset="utf-8">
<title>KTR Design Business Card</title>
<link rel="stylesheet" href="https://fonts.googleapis.com/css2?family=Open+Sans:wght@300;400;700&display=swap">
<style>
  :root {
    --page: #c9c9c9;
    --card-dark: #000000;
    --card-light: #ffffff;
    --ink-light: #ffffff;
    --ink-dark: #111111;
    --art-tone: #3a3a3a;
  }
  * { box-sizing: border-box; margin: 0; padding: 0; }
  html, body {
    width: 1200px; height: 900px; overflow: hidden;
    background: var(--page);
    font-family: "Open Sans", Arial, sans-serif;
  }
  .stage {
    position: relative; width: 1200px; height: 900px;
    display: flex; align-items: center; justify-content: center; gap: 40px;
  }
  .card {
    position: relative; width: 540px; height: 309px; overflow: hidden;
    box-shadow: 0 6px 18px rgba(0,0,0,0.25);
  }
  .card--front { background: var(--card-dark); color: var(--ink-light); }
  .card--back { background: var(--card-light); color: var(--ink-dark); }

  .name-tab {
    position: absolute; left: 150px; top: 22px; width: 190px; height: 56px;
    background: var(--card-light); color: var(--ink-dark);
    border-radius: 0 28px 28px 0;
    padding: 6px 22px 0 10px; text-align: right; z-index: 2;
  }
  .name-tab__name { font-weight: 700; font-size: 22px; line-height: 26px; letter-spacing: 0.5px; }
  .name-tab__role { font-weight: 700; font-size: 11px; line-height: 14px; }

  .contact-list { position: absolute; left: 0; top: 96px; list-style: none; z-index: 2; }
  .contact-row { position: relative; height: 34px; display: flex; align-items: center; }
  .contact-row__bar { height: 22px; background: var(--card-light); }
  .contact-row:nth-child(1) .contact-row__bar { width: 134px; }
  .contact-row:nth-child(2) .contact-row__bar { width: 114px; }
  .contact-row:nth-child(3) .contact-row__bar { width: 94px; }
  .contact-row:nth-child(4) .contact-row__bar { width: 74px; }
  .contact-row__icon {
    width: 26px; height: 26px; margin-left: -10px; border-radius: 50%;
    background: var(--card-light); border: 2px solid var(--card-dark);
    display: flex; align-items: center; justify-content: center;
  }
  .contact-row__text { margin-left: 12px; font-size: 12px; line-height: 14px; letter-spacing: 0.3px; white-space: nowrap; }

  .skyline {
    position: absolute; left: 290px; bottom: 0; width: 110px; height: 170px;
    background: linear-gradient(180deg, #2a2a2a 0%, var(--art-tone) 100%);
    z-index: 1;
  }
  .brand--front {
    position: absolute; left: 412px; top: 130px;
    font-weight: 300; font-size: 20px; letter-spacing: 1px; color: var(--ink-light);
    white-space: nowrap;
  }

  .brand--back {
    position: absolute; left: 0; right: 0; top: 100px; text-align: center;
    font-weight: 300; font-size: 56px; letter-spacing: 3px; color: var(--ink-dark);
  }
  .back-web { position: absolute; left: 40px; top: 206px; font-size: 12px; letter-spacing: 0.5px; }
  .back-mail { position: absolute; right: 40px; bottom: 32px; font-size: 13px; font-weight: 700; letter-spacing: 0.5px; }
</style>
</head>
<body>
<main class="stage">
  <section class="card card--front">
    <div class="name-tab">
      <div class="name-tab__name">Your Name</div>
      <div class="name-tab__role">Designation</div>
    </div>
    <ul class="contact-list">
      <li class="contact-row">
        <span class="contact-row__bar"></span>
        <span class="contact-row__icon">
          <svg width="12" height="14" viewBox="0 0 12 14"><path d="M6 0a5 5 0 0 0-5 5c0 4 5 9 5 9s5-5 5-9a5 5 0 0 0-5-5z" fill="#000"/><circle cx="6" cy="5" r="2" fill="#fff"/></svg>
        </span>
        <span class="contact-row__text">111,Lorem Ipsum Street,<br>LW-123</span>
      </li>
      <li class="contact-row">
        <span class="contact-row__bar"></span>
        <span class="contact-row__icon">
          <svg width="12" height="12" viewBox="0 0 12 12"><path d="M2 0l2.5 2.8-1.2 1.6a7 7 0 0 0 4.3 4.3l1.6-1.2L12 10l-2 2C4 12 0 8 0 2z" fill="#000"/></svg>
        </span>
        <span class="contact-row__text">123 456 789,987 654 321</span>
      </li>
      <li class="contact-row">
        <span class="contact-row__bar"></span>
        <span class="contact-row__icon">
          <svg width="14" height="10" viewBox="0 0 14 10"><rect x="0.5" y="0.5" width="13" height="9" fill="#000"/><path d="M0.5 0.5l6.5 5 6.5-5" stroke="#fff" fill="none"/></svg>
        </span>
        <span class="contact-row__text">yourmailid@ktrdesign.com</span>
      </li>
      <li class="contact-row">
        <span class="contact-row__bar"></span>
        <span class="contact-row__icon">
          <svg width="14" height="14" viewBox="0 0 14 14" fill="none" stroke="#000" stroke-width="1.3"><circle cx="7" cy="7" r="6"/><ellipse cx="7" cy="7" rx="2.6" ry="6"/><path d="M1 7h12M2 4h10M2 10h10"/></svg>
        </span>
        <span class="contact-row__text">yourwebsitektr.com</span>
      </li>
    </ul>
    <div class="skyline" role="img" aria-label="Dark grey line illustration of a tall skyscraper and small houses"></div>
    <div class="brand brand--front">KTR Design</div>
  </section>

  <section class="card card--back">
    <div class="brand brand--back">KTR Design</div>
    <div class="back-web">yourwebsitektr.com</div>
    <div class="back-mail">yourmailid@ktrdesign.com</div>
  </section>
</main>
</body>
</html>
```